Webpage for co-working space for tech startups

We have an established co-working space in Aalborg Denmark where we have around 30 companies sharing office space. We are starting a new chapter for us and would like to have a new graphical image - new logo and new webpage, but keep the same name. The webpage should be professional, but also "fun", not too serious. We are all about working hard on our companies, but also taking some time off in between and being social and having fun. We are not corporate, but want to project the image that we are serious about what we do.

We currently have a black/red logo (see www.hivedesk.dk or test.hivedesk.dk), but are interesting in having a new logo design, so colour can be chosen freely. Currently our logo is a big HIVE and a little desk underneath the HIVE. The new logo will be one word "hivedesk" with a small logo before or on top.

If we can make a good webpage for this project, then I have a second more simple project which is also a small single page wordpress site which I would also like to have made.

Target Market(s)

tech startups - relatively new companies, typically younger people 20-35 with a tech background - business or programming, preferably both

Industry/Entity Type

HIVE

Logo Text

hivedesk

Coding

Coded - Design and coding required

Number of Pages Required

4 page

Font styles to use
Sans Serif

Colors

Designer to choose colors to be used in the design.

Requirements
Must have
• Wordpress CMS.
• Mobile and PC optimized
• 2 languages - English and Danish
• Four sections, could be four pages, or four sections of a single page.
• "Home", "Residents", "Our Working Space", "Our Event Space"
• Footer of page or pages should have contact information.
• "Home" has some information about who we are and what we do
• "Residents" has a list of all our residents - it should be possible to easily add and removed new / old residents - See one example here: http://test.hivedesk.dk/en_GB/beboere/ or another example here: http://www.hivedesk.dk/beboere/ - one of our colleagues http://pilotbarn.dk/startups/ or another one of our colleagues http://www.brightkelpyard.dk/residents/
• "Our working space" will have a description of our building, a map of where it is and a bunch of photos which show the different offices, meeting rooms and people working
• "Our events space" will have a description of our event spaces, details of cost + different arrangments of furniture, and lots of photos of events, see here for an example http://www.hivedesk.dk/lej-vores-lokaler/
• Our current webpage - www.hivedesk.dk was put together very quickly and has not really been optimized. We started a new webpage test.hivedesk.dk, but it was never really finished.
• We are looking for a simple webpage, not too much going on. Examples of some of our colleagues in the business http://pilotbarn.dk/, http://www.brightkelpyard.dk/,
Nice to have
• http://www.brightkelpyard.dk/ is a really good template for us. If we can get something like this, we are happy.

```html
<!DOCTYPE html>
<html lang="en">
<head>
<meta charset="utf-8">
<title>Hivedesk – co-working space for startup companies</title>
<link rel="stylesheet" href="https://fonts.googleapis.com/css2?family=Raleway:wght@400;500;600&family=Open+Sans:wght@400;600&family=Roboto+Condensed:wght@400&display=swap">
<style>
:root{
  --accent:#d3243d;
  --accent-dark:#b81d33;
  --ink:#222;
  --body:#555;
  --panel:#f0f0f0;
  --white:#fff;
  --sponsor:#1d2a44;
  --news-red:#5c0009;
  --footer:#000;
}
*{box-sizing:border-box;margin:0;padding:0}
html,body{width:1200px;height:3243px;overflow:hidden}
body{font-family:"Open Sans",Arial,sans-serif;color:var(--body);background:var(--white)}
h1,h2,h3{font-family:"Raleway",Arial,sans-serif;font-weight:500;color:var(--ink)}

/* Hero */
.hero{position:relative;height:601px;color:var(--white);overflow:hidden}
.hero-photo{position:absolute;inset:0;background:linear-gradient(160deg,#4a4540 0%,#2b2826 45%,#1c1a19 100%)}
.hero-shade{position:absolute;inset:0;background:rgba(0,0,0,.25)}
.nav{position:absolute;top:46px;left:92px;right:90px;display:flex;align-items:center;justify-content:space-between}
.brand{font-family:"Open Sans",Arial,sans-serif;font-weight:600;font-size:34px;color:var(--white)}
.menu{display:flex;align-items:center;gap:26px;font-size:17px}
.menu a{color:var(--white);text-decoration:none}
.menu a.current{text-decoration:underline;text-underline-offset:4px}
.lang{border:1px solid rgba(255,255,255,.8);border-radius:3px;padding:3px 10px;font-size:14px}
.hero-title{position:absolute;top:245px;width:100%;text-align:center;font-family:"Raleway",Arial,sans-serif;font-size:86px;font-weight:400;color:var(--white)}
.hero-sub{position:absolute;top:360px;width:100%;text-align:center;font-family:"Roboto Condensed",Arial,sans-serif;font-size:36px}
.arrow{position:absolute;top:320px;width:22px;height:22px}
.arrow.left{left:72px}.arrow.right{right:72px}

/* Sections */
.section-title{text-align:center;font-size:36px}
.about{height:530px;padding-top:106px;text-align:center;overflow:hidden}
.about .quote{margin:30px auto 0;width:900px;font-family:"Raleway",Arial,sans-serif;font-size:19px;line-height:37px;color:#333}
.about .text{margin:18px auto 0;width:900px;font-size:14px;line-height:23px;color:var(--body)}
.btn{display:inline-block;margin-top:30px;background:var(--accent);color:var(--white);font-size:15px;padding:8px 22px;border-radius:3px;text-decoration:none}

.services{background:var(--panel);height:741px;padding-top:102px;overflow:hidden}
.cards{display:flex;gap:39px;justify-content:center;margin-top:68px}
.card{width:315px;height:402px;background:var(--white);padding:13px;box-shadow:0 8px 18px rgba(0,0,0,.22);text-align:center}
.card-img{height:190px}
.card h3{margin-top:26px;font-family:"Open Sans",Arial,sans-serif;font-weight:400;font-size:19px;color:var(--ink)}
.card p{margin:12px auto 0;width:240px;font-size:13px;line-height:22px}
.more{display:inline-block;margin-top:16px;color:var(--accent-dark);font-size:14px;text-decoration:none}

.news{height:490px;padding-top:105px;overflow:hidden}
.news-list{display:flex;gap:26px;justify-content:center;margin-top:45px}
.post{width:497px;height:191px;display:flex;background:var(--white);box-shadow:0 3px 10px rgba(0,0,0,.2)}
.post-img{width:162px;flex:none}
.post-body{padding:18px 20px 0 20px}
.post h3{font-family:"Open Sans",Arial,sans-serif;font-weight:400;font-size:16px;color:#333}
.post .date{margin-top:10px;font-size:13px;color:#444}
.post p{margin-top:8px;font-size:13px;line-height:20px;text-align:justify}
.post .more{margin-top:4px;font-size:13px}

.sponsors{height:312px;padding-top:40px;overflow:hidden}
.sponsor-row{display:flex;justify-content:space-around;align-items:center;margin:55px 70px 0}
.sponsor{font-family:"Open Sans",Arial,sans-serif;font-weight:600;font-size:24px;color:var(--sponsor)}

.newsletter{background:var(--news-red);height:331px;padding-top:90px;text-align:center;color:var(--white);overflow:hidden}
.newsletter h2{color:var(--white);font-size:36px;font-weight:400}
.newsletter p{margin-top:12px;font-size:15px}
.signup{display:flex;width:491px;height:41px;margin:22px auto 0}
.signup span{flex:1;background:var(--white);border-radius:5px 0 0 5px;text-align:left;padding:11px 14px;font-size:13px;color:#999}
.signup b{width:82px;background:var(--accent);border-radius:0 5px 5px 0;font-weight:400;font-size:13px;padding-top:11px}

.footer{background:var(--footer);height:238px;color:var(--white);position:relative;overflow:hidden}
.footer .brand{position:absolute;left:93px;top:64px;font-size:32px}
.socials{position:absolute;left:93px;top:120px;display:flex;gap:9px}
.socials i{width:30px;height:30px;border:2px solid var(--white);border-radius:50%}
.copy{position:absolute;left:93px;top:163px;font-size:12px}
.col{position:absolute;top:64px;font-size:13px;line-height:23px}
.col h4{font-family:"Open Sans",Arial,sans-serif;font-weight:400;font-size:16px;margin-bottom:14px;letter-spacing:.5px}
</style>
</head>
<body>

<header class="hero">
  <div class="hero-photo" role="img" aria-label="Photo of people working at long desks in an open co-working office"></div>
  <div class="hero-shade"></div>
  <nav class="nav">
    <div class="brand">Hivedesk</div>
    <div class="menu">
      <a class="current">Home</a><a>Residents</a><a>Our Working Space</a><a>Our Event Space</a>
      <span class="lang">English ▾</span>
    </div>
  </nav>
  <svg class="arrow left" viewBox="0 0 22 22"><path d="M14 4 7 11l7 7" fill="none" stroke="#fff" stroke-width="2.5"/></svg>
  <svg class="arrow right" viewBox="0 0 22 22"><path d="M8 4l7 7-7 7" fill="none" stroke="#fff" stroke-width="2.5"/></svg>
  <h1 class="hero-title">HiveDesk</h1>
  <div class="hero-sub">co-working space for startup companies</div>
</header>

<section class="about">
  <h2 class="section-title">Who We Are</h2>
  <p class="quote">"HiveDesk will create inspiration, motivation, cohesion, attention, jobs and opportunities - and thereby contribute to Aalborg and North Jutland becoming a growth center."</p>
  <p class="text">HiveDesk Fjordhus office is run by the association HiveDesk f.m.ba which is a voluntary association. The association wishes to focus on scalable entrepreneurs in Nordjylland. With the start of the office community, the association has created a physical focal point for growth entrepreneurs. Here one can meet for dialogue, sparring and knowledge sharing.</p>
  <a class="btn">View More</a>
</section>

<section class="services">
  <h2 class="section-title">What We Do</h2>
  <div class="cards">
    <article class="card">
      <div class="card-img" role="img" aria-label="Photo of a shared office with brick wall and bookshelves" style="background:linear-gradient(135deg,#8a4a2c,#c48a52 60%,#6b5140)"></div>
      <h3>Residents</h3>
      <p>The corporate community at HiveDesk is a community of tech entrepreneurs with global growth</p>
      <a class="more">Read More »</a>
    </article>
    <article class="card">
      <div class="card-img" role="img" aria-label="Photo of a bright office with white desks and black chairs" style="background:linear-gradient(180deg,#f1f2f2,#d6d8d9 70%,#9a9c9e)"></div>
      <h3>Our Working Space</h3>
      <p>The corporate community at HiveDesk is a community of tech entrepreneurs with global growth</p>
      <a class="more">Read More »</a>
    </article>
    <article class="card">
      <div class="card-img" role="img" aria-label="Photo of an empty event hall with wooden ceiling beams" style="background:linear-gradient(180deg,#6b4a22,#c9a46a 45%,#a5a190)"></div>
      <h3>Our Event Space</h3>
      <p>The corporate community at HiveDesk is a community of tech entrepreneurs with global growth</p>
      <a class="more">Read More »</a>
    </article>
  </div>
</section>

<section class="news">
  <h2 class="section-title">Latest News</h2>
  <div class="news-list">
    <article class="post">
      <div class="post-img" role="img" aria-label="Photo of a meeting room with a wooden table" style="background:linear-gradient(135deg,#cfcfcf,#7a7a7a)"></div>
      <div class="post-body">
        <h3>Quisquam est qui dolorem</h3>
        <div class="date">09-07-2018</div>
        <p>Lorem Ipsum has been the industry's standard dummy text ever since the 1500s, when an unknown printer</p>
        <a class="more">Read More &gt;&gt;</a>
      </div>
    </article>
    <article class="post">
      <div class="post-img" role="img" aria-label="Photo of an empty stage with spotlights" style="background:linear-gradient(180deg,#2a2a2a,#8c8c8c 70%,#d8d8d8)"></div>
      <div class="post-body">
        <h3>Dolorem ipsum quia dolor</h3>
        <div class="date">09-07-2018</div>
        <p>Lorem Ipsum has been the industry's standard dummy text ever since the 1500s, when an unknown printer</p>
        <a class="more">Read More &gt;&gt;</a>
      </div>
    </article>
  </div>
</section>

<section class="sponsors">
  <h2 class="section-title">Sponsors</h2>
  <div class="sponsor-row">
    <div class="sponsor">Northvale IP</div>
    <div class="sponsor">Kestrup</div>
    <div class="sponsor">Fjordline Bank</div>
    <div class="sponsor">Holm Sander</div>
  </div>
</section>

<section class="newsletter">
  <h2>Subscribe to our newsletter</h2>
  <p>Sed velit sapien, commodo et dictum porta, varius id nibh.</p>
  <div class="signup"><span>Your email address</span><b>Subscribe</b></div>
</section>

<footer class="footer">
  <div class="brand">Hivedesk</div>
  <div class="socials"><i></i><i></i><i></i><i></i><i></i></div>
  <div class="copy">Copyright © 2018 All Rights Reserved</div>
  <div class="col" style="left:391px">
    <h4>VISIT US</h4>
    Hive Desk fmba<br>Havnegade 14<br>9000 Aalborg, Denmark
  </div>
  <div class="col" style="left:625px">
    <h4>CALL US</h4>
    (+45) 20 00 11 22<br>Monday-Friday at, 9: 00-16: 00<br>info@hivedesk.dk
  </div>
  <div class="col" style="left:897px">
    <h4>OPENING HOURS</h4>
    For residents: 24-7, all weekdays.<br>For guests: 9: 00-16: 00,<br>&nbsp;Monday-Friday.
  </div>
</footer>

</body>
</html>
```